Bramblewick Forage Business Cards

I need a business card with my logo, number, Facebook account, and some information about what I am selling. Green card with logo on the front. 555-214-8392 phone number, @bramblewickforage Facebook, •Orchardgrass Hay •Alfalfa Hay •Mixed Grass Hay , and “Premium Quality Hay” all written on the back.

Target Market(s)

Hay

Contact Information for Business Card

Phone number, Facebook, different types of hay.

Colors
00AB8E
00BBA5
67D7C9
C6EFE9
E9F9F6

```html
<!DOCTYPE html>
<html lang="en">
<head>
<meta charset="utf-8">
<title>Bramblewick Forage Business Cards</title>
<link href="https://fonts.googleapis.com/css2?family=Arimo:wght@400;700&family=Yellowtail&display=swap" rel="stylesheet">
<style>
  :root {
    --backdrop: #e4e4e2;
    --card-white: #f7f7f5;
    --green: #16a34f;
    --green-deep: #0c7f3a;
    --green-light: #3fbf72;
    --green-pale: #cdeed9;
    --ink: #262626;
    --ink-soft: #3a3a3a;
    --white: #ffffff;
  }
  * { box-sizing: border-box; margin: 0; padding: 0; }
  html, body {
    width: 1200px; height: 801px; overflow: hidden;
    background: var(--backdrop);
    font-family: "Arimo", Arial, sans-serif;
  }
  .canvas {
    position: relative; width: 1200px; height: 801px;
    display: flex; align-items: center; justify-content: center; gap: 50px;
  }
  .card {
    position: relative; width: 525px; height: 300px; overflow: hidden;
    box-shadow: 0 6px 18px rgba(0,0,0,0.18);
  }

  /* Front */
  .card--front { background: var(--card-white); border-bottom: 6px solid var(--green); }
  .front__tab {
    position: absolute; left: 118px; bottom: 0; width: 36px; height: 14px;
    background: var(--green);
  }
  .front__decoration {
    position: absolute; right: 20px; top: 30px; width: 230px; height: 200px;
    border-radius: 50%;
    background: radial-gradient(ellipse at center, rgba(22,163,79,0.18), rgba(22,163,79,0.04) 70%, transparent 75%);
  }
  .brand {
    position: absolute; left: 36px; top: 44px;
    display: flex; align-items: center; gap: 12px;
  }
  .brand__mark { width: 34px; height: 34px; background: var(--green); }
  .brand__name { font-weight: 700; font-size: 24px; color: var(--ink); }
  .person { position: absolute; left: 36px; top: 138px; }
  .person__name {
    font-family: "Yellowtail", cursive; font-size: 36px; color: var(--green); line-height: 1;
  }
  .person__role { font-size: 17px; color: var(--ink); margin-top: 2px; }
  .contacts { position: absolute; left: 36px; top: 214px; list-style: none; }
  .contacts__item {
    display: flex; align-items: center; gap: 10px;
    font-size: 19px; color: var(--ink-soft); margin-bottom: 6px;
  }
  .contacts__icon { width: 18px; height: 18px; flex: none; }
  .contacts__square { width: 16px; height: 16px; background: var(--green); border-radius: 3px; flex: none; }

  /* Back */
  .card--back {
    background: linear-gradient(135deg, var(--green-deep) 0%, var(--green) 45%, var(--green-light) 60%, var(--green) 80%, var(--green-deep) 100%);
  }
  .back__illustration {
    position: absolute; left: 0; top: 20px; width: 330px; height: 270px;
    border-radius: 40% 55% 30% 20%;
    background: linear-gradient(160deg, rgba(8,90,40,0.55), rgba(63,191,114,0.35));
  }
  .back__info { position: absolute; right: 34px; top: 112px; color: var(--white); }
  .back__brand { font-weight: 700; font-size: 26px; margin-bottom: 12px; }
  .products { list-style: none; }
  .products__item {
    display: flex; align-items: center; gap: 8px;
    font-size: 15px; letter-spacing: 0.3px; margin-bottom: 5px; text-transform: uppercase;
  }
  .products__bullet { width: 7px; height: 7px; border-radius: 50%; background: var(--white); flex: none; }
</style>
</head>
<body>
<main class="canvas">
  <section class="card card--front">
    <div class="front__decoration" role="img" aria-label="Faint large brand emblem decoration"></div>
    <div class="brand">
      <span class="brand__mark"></span>
      <span class="brand__name">Bramblewick Forage</span>
    </div>
    <div class="person">
      <p class="person__name">Marcus Ellery</p>
      <p class="person__role">Manager</p>
    </div>
    <ul class="contacts">
      <li class="contacts__item">
        <svg class="contacts__icon" viewBox="0 0 24 24" aria-hidden="true">
          <path fill="#16a34f" d="M6.6 10.8a15.1 15.1 0 0 0 6.6 6.6l2.2-2.2c.3-.3.7-.4 1-.2 1.1.4 2.3.6 3.6.6.6 0 1 .4 1 1V20c0 .6-.4 1-1 1A17 17 0 0 1 3 4c0-.6.4-1 1-1h3.5c.6 0 1 .4 1 1 0 1.3.2 2.5.6 3.6.1.3 0 .7-.2 1z"/>
        </svg>
        555-214-8392
      </li>
      <li class="contacts__item">
        <span class="contacts__square"></span>
        @bramblewickforage
      </li>
    </ul>
    <span class="front__tab"></span>
  </section>

  <section class="card card--back">
    <div class="back__illustration" role="img" aria-label="Embossed silhouette of a galloping horse"></div>
    <div class="back__info">
      <p class="back__brand">Bramblewick Forage</p>
      <ul class="products">
        <li class="products__item"><span class="products__bullet"></span>Orchardgrass Hay</li>
        <li class="products__item"><span class="products__bullet"></span>Alfalfa Hay</li>
        <li class="products__item"><span class="products__bullet"></span>Mixed Grass Hay</li>
        <li class="products__item"><span class="products__bullet"></span>Premium Quality Hay</li>
      </ul>
    </div>
  </section>
</main>
</body>
</html>
```